Home Loan Introducer needs logo/business cards

We need a simple but classy logo for business cards and flyers. The business is a home loan referral business that is called an Introducer. The business name is "The Harborline".
I was thinking very simple and straight to the point on the front with "Home Loans" the only thing on the front with a nice background colour/s.
Then on the back, "The Harborline"
and "Quality Customer Service"
and "Email, text or call welcome"
and then my name, email address and phone number.
Updates
Thank you for all the designs :-)
Target Market(s)
Home buyers.
Home owners.
Investors.
Industry/Entity Type
Loan
Look and feel

```html
<!DOCTYPE html>
<html lang="en">
<head>
<meta charset="utf-8">
<title>The Harborline – Business Cards</title>
<link rel="stylesheet" href="https://fonts.googleapis.com/css2?family=Exo+2:ital,wght@0,400;0,600;0,700;1,500&display=swap">
<style>
  :root {
    --backdrop: #7a4524;
    --card-dark: #232323;
    --card-dark-back: #262626;
    --amber: #fbae3c;
    --amber-light: #fde0b0;
    --brand-blue: #1b6fc2;
    --ink: #111111;
    --white: #ffffff;
    --font: "Exo 2", Arial, sans-serif;
  }
  * { box-sizing: border-box; margin: 0; padding: 0; }
  html, body {
    width: 1200px; height: 750px; overflow: hidden;
    background: var(--backdrop);
    font-family: var(--font);
  }
  .canvas { position: relative; width: 1200px; height: 750px; }

  .card {
    position: absolute;
    overflow: hidden;
    box-shadow: 0 8px 22px rgba(0,0,0,.45);
  }

  /* Contact side */
  .card-contact {
    left: 165px; top: 50px; width: 545px; height: 320px;
    background: var(--card-dark);
  }
  .card-contact .amber-band {
    position: absolute; left: 0; right: 0; top: 190px; bottom: 0;
    background: var(--amber);
  }
  .card-contact .house-art {
    position: absolute; left: 0; top: 190px; width: 270px; height: 130px;
    background: linear-gradient(160deg, var(--amber-light) 0%, var(--amber) 90%);
  }
  .brand {
    position: absolute; left: 190px; top: 30px; width: 200px;
    display: flex; flex-direction: column; align-items: center; gap: 10px;
  }
  .brand-dot {
    width: 56px; height: 56px; border-radius: 50%;
    background: var(--brand-blue);
  }
  .brand-name {
    width: 100%; padding: 4px 0 3px;
    background: var(--amber); border-radius: 4px;
    text-align: center;
    font-weight: 700; font-size: 20px; letter-spacing: .5px;
    color: var(--white);
  }
  .contact {
    position: absolute; right: 20px; top: 200px; width: 200px;
    text-align: right;
  }
  .perks { list-style: none; text-align: left; margin-bottom: 8px; }
  .perks li {
    display: flex; align-items: center; gap: 4px;
    font-style: italic; font-weight: 500; font-size: 14px;
    color: var(--brand-blue); line-height: 1.4;
  }
  .perks svg { flex: none; }
  .person {
    font-weight: 600; font-size: 19px; color: var(--ink);
    text-align: center; padding-bottom: 3px;
    border-bottom: 2px solid var(--white);
    margin-bottom: 4px;
  }
  .details { font-size: 9.5px; color: var(--ink); text-align: center; line-height: 1.35; }
  .details span { color: var(--brand-blue); }

  /* Headline side */
  .card-headline {
    left: 585px; top: 395px; width: 510px; height: 310px;
    background: var(--card-dark-back);
  }
  .card-headline .houses-art {
    position: absolute; left: 105px; top: 35px; width: 300px; height: 125px;
    background: radial-gradient(ellipse at 50% 60%, #333333 0%, var(--card-dark-back) 75%);
  }
  .headline {
    position: absolute; left: 28px; right: 28px; top: 155px; height: 76px;
    background: var(--amber); border-radius: 6px;
    display: flex; align-items: center; justify-content: center;
    font-weight: 700; font-size: 56px; letter-spacing: 1px;
    color: var(--white);
  }
</style>
</head>
<body>
<main class="canvas">

  <section class="card card-contact">
    <div class="amber-band"></div>
    <div class="house-art" role="img" aria-label="Large faint house illustration"></div>

    <div class="brand">
      <div class="brand-dot"></div>
      <div class="brand-name">THE HARBORLINE</div>
    </div>

    <div class="contact">
      <ul class="perks">
        <li>
          <svg width="14" height="14" viewBox="0 0 14 14"><path d="M2 7.5 L5.5 11 L12 2.5" fill="none" stroke="#111" stroke-width="2.4" stroke-linecap="round" stroke-linejoin="round"/></svg>
          Quality Costumer Service
        </li>
        <li>
          <svg width="14" height="14" viewBox="0 0 14 14"><path d="M2 7.5 L5.5 11 L12 2.5" fill="none" stroke="#111" stroke-width="2.4" stroke-linecap="round" stroke-linejoin="round"/></svg>
          Email, text or call welcome
        </li>
      </ul>
      <p class="person">Daniel Marsh</p>
      <p class="details">Phone: <span>+6391045278</span><br>Email: <span>d.marsh@harborline.com</span></p>
    </div>
  </section>

  <section class="card card-headline">
    <div class="houses-art" role="img" aria-label="Faint row of three house silhouettes"></div>
    <h1 class="headline">HOME LOAN</h1>
  </section>

</main>
</body>
</html>
```